Business card for law firm

Need business card for new law firm. Think confident, authoritative, conservative, but not stuffy or old-fashioned.

Contact Information for Business Card

Content for card - logo (uploaded), plus the following:

Paul Whitcombe (larger font)
Managing Partner (larger font, but not as large as name)
Level 9, 7 Ferris Lane
Sydney NSW 2000
Main Tel 02 9364 2710
Direct Tel 02 8472 3159
Email paul@qvlegal.com.au
www.qvlegal.com.au

Letterhead design should include logo plus:
Level 9, 7 Ferris Lane
Sydney NSW 2000
Tel 02 8472 3159
www.qvlegal.com.au

```html
<!DOCTYPE html>
<html lang="en">
<head>
<meta charset="utf-8">
<title>Quayview Legal – Business Card</title>
<link href="https://fonts.googleapis.com/css2?family=PT+Sans:wght@400;700&family=PT+Sans+Narrow:wght@700&display=swap" rel="stylesheet">
<style>
  :root {
    --backdrop: #8c8b8b;
    --card: #fbfbfa;
    --card-edge: #2f5fc4;
    --navy: #111c5a;
    --ink: #1c1c1c;
    --muted: #4a4a4a;
  }
  * { box-sizing: border-box; margin: 0; padding: 0; }
  html, body {
    width: 1200px;
    height: 904px;
    overflow: hidden;
    background: var(--backdrop);
  }
  .stage {
    width: 1200px;
    height: 904px;
    display: flex;
    align-items: center;
    justify-content: center;
  }
  .card {
    width: 500px;
    height: 820px;
    background: var(--card);
    border: 3px solid var(--card-edge);
    display: flex;
    flex-direction: column;
    align-items: center;
    text-align: center;
    padding-top: 120px;
    font-family: "PT Sans", "Helvetica Neue", Arial, sans-serif;
  }
  .firm {
    display: flex;
    align-items: center;
    gap: 18px;
    color: var(--navy);
    font-weight: 400;
    font-size: 40px;
    letter-spacing: 0.06em;
    text-transform: uppercase;
  }
  .firm-mark {
    width: 40px;
    height: 40px;
    background: var(--navy);
    flex: none;
  }
  .person { margin-top: 110px; }
  .person-name {
    font-family: "PT Sans Narrow", "Arial Narrow", sans-serif;
    font-weight: 700;
    font-size: 52px;
    line-height: 1;
    color: var(--navy);
  }
  .person-role {
    font-weight: 700;
    font-size: 28px;
    line-height: 1.2;
    color: var(--ink);
    margin-top: 4px;
  }
  .divider {
    width: 90px;
    height: 2px;
    background: var(--navy);
    margin: 34px 0 22px;
  }
  .details {
    font-size: 21px;
    line-height: 1.35;
    color: var(--muted);
  }
  .website {
    margin-top: 30px;
    font-weight: 700;
    font-size: 22px;
    color: var(--ink);
  }
</style>
</head>
<body>
<main class="stage">
  <article class="card">
    <div class="firm">
      <span class="firm-mark"></span>
      <span class="firm-name">Quayview Legal</span>
    </div>

    <div class="person">
      <h1 class="person-name">Paul Whitcombe</h1>
      <p class="person-role">Managing Partner</p>
    </div>

    <span class="divider"></span>
    <address class="details" style="font-style:normal">
      Level 9, 7 Ferris Lane<br>
      Sydney NSW 2000
    </address>

    <span class="divider"></span>
    <p class="details">
      02 9364 2710 (Main)<br>
      02 8472 3159 (Direct)<br>
      paul@qvlegal.com.au
    </p>

    <p class="website">qvlegal.com.au</p>
  </article>
</main>
</body>
</html>
```